Pemberlux: Smart Quotes for Wine Lovers

Hello. I am completing book of quotes for wine lovers. Need the text formatted so that it is easy to read and aesthetically pleasing...modern, clean, smart. Number the pages. The cover is complete. Book is small square. 7.5 by 7.5 inches. If you want to show me first few pages that would be awesome. Thank you!
Updates

I edited the quotes so if you downloaded first ones, please grab these ones instead, thank you! 

Target Market(s)

wine lovers. Urban. Modern.

Industry/Entity Type

Quotes

Requirements
Should not have
• No color. black and white only.

```html
<!DOCTYPE html>
<html lang="en">
<head>
<meta charset="utf-8">
<title>Pemberlux: Smart Quotes for Wine Lovers — Spread 28–29</title>
<link rel="stylesheet" href="https://fonts.googleapis.com/css2?family=Sorts+Mill+Goudy&family=PT+Sans:wght@400;700&display=swap">
<style>
  :root {
    --ink: #000000;
    --paper: #ffffff;
    --serif: "Sorts Mill Goudy", "Goudy Old Style", Georgia, serif;
    --sans: "PT Sans", "Gill Sans", Arial, sans-serif;
  }
  * { margin: 0; padding: 0; box-sizing: border-box; }
  html, body {
    width: 1200px;
    height: 600px;
    overflow: hidden;
    background: var(--paper);
  }
  .spread {
    position: relative;
    width: 1200px;
    height: 600px;
    display: flex;
  }
  .page {
    position: relative;
    height: 600px;
  }
  .page--dark {
    width: 602px;
    background: var(--ink);
    color: var(--paper);
  }
  .page--light {
    width: 598px;
    background: var(--paper);
    color: var(--ink);
  }
  .quote {
    position: absolute;
    font-family: var(--serif);
    font-size: 37px;
    line-height: 45.5px;
    font-weight: 400;
  }
  .page--dark .quote {
    left: 95px;
    top: 133px;
    width: 320px;
  }
  .page--light .quote {
    right: 94px;
    top: 133px;
    text-align: right;
    width: 290px;
  }
  .attribution {
    position: absolute;
    font-family: var(--sans);
    font-size: 13px;
    letter-spacing: 0.08em;
    text-transform: uppercase;
  }
  .page--dark .attribution { left: 95px; top: 326px; }
  .page--light .attribution { right: 94px; top: 320px; }
  .biography {
    position: absolute;
    font-family: var(--sans);
    font-weight: 700;
    font-size: 7.6px;
    line-height: 9.5px;
    white-space: nowrap;
  }
  .page--dark .biography {
    right: 64px;
    top: 517px;
    text-align: right;
  }
  .page--light .biography {
    left: 60px;
    top: 517px;
  }
  .folio {
    position: absolute;
    right: 79px;
    top: 522px;
    font-family: var(--sans);
    font-size: 14px;
  }
</style>
</head>
<body>
  <main class="spread">
    <section class="page page--dark">
      <blockquote class="quote">The connoisseur does not drink wine but tastes its secrets</blockquote>
      <p class="attribution">–Mateo Ferran</p>
      <p class="biography">Mateo Ignasi Ferran i Costa, painter of coastal dreamscapes and<br>keen collector of old vintages (1911–1978) Catalan Artist.</p>
    </section>
    <section class="page page--light">
      <blockquote class="quote">Wine is the divine juice of September.</blockquote>
      <p class="attribution">–Lucien Arvel</p>
      <p class="biography">Jean-Baptiste Morel &nbsp;known by his “nom de plume” Lucien Arvel.<br>(1702 –1781). Provincial Essayist, Playwright and Amateur Vintner.</p>
      <span class="folio">29</span>
    </section>
  </main>
</body>
</html>
```